Business card for law firm

Need business card for new law firm. Think confident, authoritative, conservative, but not stuffy or old-fashioned.

Contact Information for Business Card

Content for card - logo (uploaded), plus the following:

Paul Whitcombe (larger font)
Managing Partner (larger font, but not as large as name)
Level 9, 7 Ferris Lane
Sydney NSW 2000
Main Tel 02 9364 2710
Direct Tel 02 8472 3159
Email paul@qvlegal.com.au
www.qvlegal.com.au

Letterhead design should include logo plus:
Level 9, 7 Ferris Lane
Sydney NSW 2000
Tel 02 8472 3159
www.qvlegal.com.au

```html
<!DOCTYPE html>
<html lang="en">
<head>
<meta charset="utf-8">
<title>Quayvale Lawyers – Business Card</title>
<link rel="stylesheet" href="https://fonts.googleapis.com/css2?family=Cinzel:wght@400&family=Open+Sans:wght@400;700&display=swap">
<style>
  :root {
    --navy: #0f1f5c;
    --ink: #2b2b2b;
    --rule: #dcdcdc;
    --paper: #ffffff;
    --backdrop: #e9e6e3;
    --black: #141414;
  }
  * { margin: 0; padding: 0; box-sizing: border-box; }
  html, body { width: 1200px; height: 997px; overflow: hidden; }
  body {
    background: var(--backdrop);
    display: flex;
    flex-direction: column;
    align-items: center;
    justify-content: center;
    gap: 60px;
  }
  .card {
    position: relative;
    width: 560px;
    height: 320px;
    overflow: hidden;
    box-shadow: 0 6px 18px rgba(0,0,0,0.12);
  }
  .card--front { background: var(--paper); }
  .card--back { background: var(--navy); color: #fff; }

  .front-swoosh { position: absolute; inset: 0; width: 100%; height: 100%; }

  .brand {
    position: absolute;
    display: flex;
    flex-direction: column;
    align-items: center;
    font-family: "Cinzel", serif;
    font-weight: 400;
  }
  .brand__row { display: flex; align-items: center; gap: 10px; }
  .brand__square { width: 14px; height: 14px; }
  .brand__name { letter-spacing: 1px; line-height: 1; }
  .brand__sub { letter-spacing: 9px; line-height: 1; margin-top: 6px; }

  .card--front .brand { left: 30px; top: 98px; width: 240px; color: var(--black); }
  .card--front .brand__square { background: var(--navy); }
  .card--front .brand__name { font-size: 30px; }
  .card--front .brand__sub { font-size: 11px; }

  .contact {
    position: absolute;
    left: 300px;
    top: 22px;
    padding-left: 16px;
    border-left: 1px solid var(--rule);
    font-family: "Open Sans", sans-serif;
    color: var(--ink);
    font-size: 11.5px;
    line-height: 1.45;
  }
  .contact__name {
    font-weight: 700;
    font-size: 16px;
    color: var(--navy);
    text-transform: uppercase;
    line-height: 1.2;
  }
  .contact__role { font-size: 12.5px; margin-bottom: 8px; }
  .contact__address { margin-bottom: 6px; }
  .contact__line { display: flex; align-items: center; gap: 6px; }
  .contact__line svg { width: 10px; height: 10px; fill: var(--ink); flex: none; }

  .card--back .brand { left: 0; right: 0; top: 90px; color: #fff; }
  .card--back .brand__square { background: #fff; width: 18px; height: 18px; }
  .card--back .brand__name { font-size: 40px; }
  .card--back .brand__sub { font-size: 13px; letter-spacing: 12px; margin-top: 8px; }
  .back-url {
    position: absolute;
    left: 0; right: 0; bottom: 62px;
    text-align: center;
    font-family: "Open Sans", sans-serif;
    font-size: 13px;
    letter-spacing: 2px;
    color: #fff;
  }
</style>
</head>
<body>

  <section class="card card--front">
    <svg class="front-swoosh" viewBox="0 0 560 320" preserveAspectRatio="none" aria-hidden="true">
      <path d="M0,268 C170,256 360,218 560,204 L560,220 C380,264 200,302 0,320 Z" fill="var(--navy)"/>
      <path d="M0,260 C170,248 360,208 560,194" fill="none" stroke="var(--black)" stroke-width="3"/>
    </svg>

    <div class="brand">
      <div class="brand__row">
        <span class="brand__square"></span>
        <span class="brand__name">Quayvale</span>
      </div>
      <span class="brand__sub">LAWYERS</span>
    </div>

    <div class="contact">
      <p class="contact__name">Paul Whitcombe</p>
      <p class="contact__role">Managing Partner</p>
      <p class="contact__address">Level 9, 7 Ferris Lane<br>Sydney NSW 2000</p>
      <p class="contact__line">
        <svg viewBox="0 0 10 10"><path d="M2,0.5 L3.6,2.6 L2.7,3.6 C3.3,5 4.9,6.6 6.4,7.3 L7.4,6.4 L9.5,8 L8.4,9.5 C4.6,9.2 0.8,5.4 0.5,1.6 Z"/></svg>
        02 9364 2710 (Main)
      </p>
      <p class="contact__line">
        <svg viewBox="0 0 10 10"><path d="M2,0.5 L3.6,2.6 L2.7,3.6 C3.3,5 4.9,6.6 6.4,7.3 L7.4,6.4 L9.5,8 L8.4,9.5 C4.6,9.2 0.8,5.4 0.5,1.6 Z"/></svg>
        02 8472 3159 (Direct)
      </p>
      <p class="contact__line">
        <svg viewBox="0 0 10 10"><path d="M0.5,2 H9.5 V8.5 H0.5 Z M1,2.4 L5,5.6 L9,2.4" stroke="#fff" stroke-width="0.8"/></svg>
        paul@qvlegal.com.au
      </p>
      <p class="contact__line">
        <svg viewBox="0 0 10 10"><circle cx="5" cy="5" r="4.5"/><path d="M0.5,5 H9.5 M5,0.5 C2.5,3 2.5,7 5,9.5 M5,0.5 C7.5,3 7.5,7 5,9.5" fill="none" stroke="#fff" stroke-width="0.7"/></svg>
        www.qvlegal.com.au
      </p>
    </div>
  </section>

  <section class="card card--back">
    <div class="brand">
      <div class="brand__row">
        <span class="brand__square"></span>
        <span class="brand__name">Quayvale</span>
      </div>
      <span class="brand__sub">LAWYERS</span>
    </div>
    <p class="back-url">www.qvlegal.com.au</p>
  </section>

</body>
</html>
```